Kestrel Facilities Business Card Design

We would now like to design business cards with the new Kestrel Facilities logo

Target Market(s)

Professional

Industry/Entity Type

Professional services

Contact Information for Business Card

Employee name, title, phone number, email address, corporate office address and logo.

Font styles to use
Sans Serif

Colors
0054AA
0677BA
7BADD7
CADEEF
E8F1F8

Requirements
Must have
• My logo
Should not have
• any other pictures or images besides my logo

```html
<!DOCTYPE html>
<html lang="en">
<head>
<meta charset="utf-8">
<title>Kestrel Facilities Business Card</title>
<link href="https://fonts.googleapis.com/css2?family=Inter:wght@400;600;700&display=swap" rel="stylesheet">
<style>
  :root {
    --brand-blue: #0a7be6;
    --deep-blue: #0a3fd6;
    --cyan: #14d6f2;
    --text-grey: #4a4a4a;
    --card-white: #ffffff;
    --backdrop: #e6e6e6;
  }
  * { margin: 0; padding: 0; box-sizing: border-box; }
  html, body {
    width: 1200px; height: 1200px; overflow: hidden;
    background: var(--backdrop);
    font-family: "Inter", Arial, sans-serif;
  }
  .card {
    position: absolute; left: 262px; width: 686px; height: 392px;
    box-shadow: 0 18px 24px rgba(0,0,0,0.18);
  }
  .card-front { top: 165px; background: var(--card-white); }
  .card-back {
    top: 653px;
    background: linear-gradient(90deg, #0b8ff0 0%, #0a7be6 55%, #0a62e2 100%);
  }
  .card-back .pattern-area {
    position: absolute; inset: 8px 6px;
    background: linear-gradient(90deg, rgba(20,214,242,0.55) 0%, rgba(10,123,230,0.2) 50%, rgba(10,63,214,0.6) 100%);
  }
  .brand {
    position: absolute; left: 437px; top: 66px; width: 199px;
    display: flex; align-items: center; gap: 12px;
  }
  .brand-square { width: 26px; height: 26px; background: var(--brand-blue); flex: none; }
  .brand-name {
    color: var(--brand-blue); font-weight: 700; font-size: 30px; line-height: 1.05;
  }
  .accent-bar {
    position: absolute; left: 0; top: 216px; width: 10px; height: 61px;
    background: var(--brand-blue);
  }
  .person-name {
    position: absolute; left: 49px; top: 212px;
    color: var(--brand-blue); font-weight: 700; font-size: 26px; letter-spacing: 0.2px;
  }
  .person-title {
    position: absolute; left: 49px; top: 243px;
    color: var(--text-grey); font-size: 17px;
  }
  .divider {
    position: absolute; left: 49px; top: 272px; width: 586px; height: 3px;
    background: var(--brand-blue);
  }
  .contact-list {
    position: absolute; left: 49px; top: 287px; list-style: none;
    color: var(--text-grey); font-size: 17px; line-height: 21.5px;
  }
  .contact-list li { display: flex; align-items: center; gap: 9px; }
  .contact-list svg { width: 14px; height: 14px; fill: var(--brand-blue); flex: none; }
  .office-address {
    position: absolute; right: 52px; top: 287px; text-align: right;
    color: var(--text-grey); font-size: 17px; line-height: 21.5px; font-style: normal;
  }
</style>
</head>
<body>
  <section class="card card-front">
    <div class="brand">
      <span class="brand-square"></span>
      <span class="brand-name">Kestrel Facilities</span>
    </div>
    <div class="accent-bar"></div>
    <h1 class="person-name">DANIEL HARLOW</h1>
    <p class="person-title">President</p>
    <div class="divider"></div>
    <ul class="contact-list">
      <li>
        <svg viewBox="0 0 24 24" aria-hidden="true"><path d="M6.6 10.8a15.1 15.1 0 0 0 6.6 6.6l2.2-2.2a1 1 0 0 1 1-.25 11.4 11.4 0 0 0 3.6.57 1 1 0 0 1 1 1V20a1 1 0 0 1-1 1A17 17 0 0 1 3 4a1 1 0 0 1 1-1h3.5a1 1 0 0 1 1 1c0 1.25.2 2.45.57 3.57a1 1 0 0 1-.25 1z"/></svg>
        555-014-2270
      </li>
      <li>
        <svg viewBox="0 0 24 24" aria-hidden="true"><path d="M2 5h20v14H2zm2 2v.5l8 5 8-5V7l-8 5z"/></svg>
        info@kestrelfacilities.com
      </li>
      <li>
        <svg viewBox="0 0 24 24" aria-hidden="true"><circle cx="12" cy="12" r="10"/><path d="M7 7c2 1 3 3 2 5s1 3 2 5M15 4c-1 2 1 3 3 3M14 13c2 0 3 2 4 4" stroke="#fff" stroke-width="1.6" fill="none"/></svg>
        kestrelfacilities.com
      </li>
    </ul>
    <address class="office-address">
      Kestrel Facilities LLC<br>
      1420 Alder Court<br>
      Alaska 34512
    </address>
  </section>

  <section class="card card-back">
    <div class="pattern-area" role="img" aria-label="Repeating brand mark pattern in cyan to deep blue tones"></div>
  </section>
</body>
</html>
```